Flowmark Engineering Business Card

our company has just rebranded and taken on a new logo design. We now need to update our business cards with the new logo. This is also an opportunity to reformat and modernize our look. We are an engineering company so the look needs to be formal and professional yet it should look modern. Have a look at our current card and the new card should have the same information.

Target Market(s)

Engineering firms, government, mining companies

Industry/Entity Type

Mechanical Engineering

Contact Information for Business Card

see example attached

Requirements
Must have
• look professional and modern
Should not have
• should not include the office locations 'Brisbane, Sydney and Kuala Lumpur'
• you will find this on the example but it should not be included in these versions. please remove from your submissions and resubmit

```html
<!DOCTYPE html>
<html lang="en">
<head>
<meta charset="utf-8">
<title>Flowmark Engineering – Business Card</title>
<link rel="stylesheet" href="https://fonts.googleapis.com/css2?family=Exo+2:wght@400;500;600;700&display=swap">
<style>
  :root {
    --page-bg: #e9e9ea;
    --card-bg: #ffffff;
    --brand-navy: #2f3f9f;
    --brand-cyan: #1ea3e3;
    --blue-deep: #2a47b3;
    --blue-bright: #1598df;
    --ink: #2b2b2b;
    --ink-soft: #444a52;
    --swoosh-dark: #2c2c2e;
    --swoosh-light: #9a9a9e;
  }
  * { margin: 0; padding: 0; box-sizing: border-box; }
  html, body {
    width: 1200px; height: 900px; overflow: hidden;
    background: var(--page-bg);
    font-family: "Exo 2", "Segoe UI", sans-serif;
  }
  .card {
    position: absolute; left: 75px; top: 150px;
    width: 1050px; height: 600px;
    background: var(--card-bg);
    overflow: hidden;
    box-shadow: 0 10px 30px rgba(0,0,0,0.12);
  }
  .card-shapes { position: absolute; inset: 0; }

  .brand {
    position: absolute; left: 90px; top: 215px;
    display: flex; align-items: center; gap: 22px;
  }
  .brand-dot {
    width: 78px; height: 78px; border-radius: 50%;
    border: 7px solid var(--brand-navy);
  }
  .brand-name {
    color: var(--brand-navy); font-weight: 700; line-height: 1;
  }
  .brand-name .line-main { display: block; font-size: 66px; letter-spacing: 1px; }
  .brand-name .line-sub { display: block; font-size: 24px; letter-spacing: 13px; margin-top: 8px; padding-left: 22px; }

  .holder {
    position: absolute; right: 60px; top: 62px; text-align: right;
  }
  .holder-name {
    color: var(--brand-cyan); font-size: 30px; font-weight: 500; letter-spacing: 3px;
  }
  .holder-role {
    color: var(--ink); font-size: 21px; font-weight: 500; margin-top: 2px;
  }

  .contact-list {
    position: absolute; right: 36px; top: 158px; list-style: none;
  }
  .contact-item {
    display: flex; justify-content: flex-end; align-items: center; gap: 14px;
    height: 30px; color: var(--ink-soft); font-size: 18px; letter-spacing: 1px;
  }
  .contact-item svg { width: 18px; height: 18px; flex: none; }

  .address {
    position: absolute; left: 56px; bottom: 42px;
    color: #ffffff; font-size: 24px; font-weight: 500; line-height: 1.3; letter-spacing: 0.5px;
  }
</style>
</head>
<body>
  <article class="card">
    <svg class="card-shapes" viewBox="0 0 1050 600" aria-hidden="true">
      <defs>
        <linearGradient id="blueBand" x1="0" y1="1" x2="1" y2="0">
          <stop offset="0" stop-color="var(--blue-deep)"/>
          <stop offset="0.55" stop-color="var(--blue-bright)"/>
          <stop offset="1" stop-color="var(--blue-deep)"/>
        </linearGradient>
        <linearGradient id="greySwoosh" x1="0" y1="0" x2="1" y2="0">
          <stop offset="0" stop-color="var(--swoosh-light)"/>
          <stop offset="1" stop-color="var(--swoosh-dark)"/>
        </linearGradient>
        <linearGradient id="cornerTab" x1="0" y1="0" x2="1" y2="0">
          <stop offset="0" stop-color="#3a3a3c"/>
          <stop offset="0.5" stop-color="#8c8c90"/>
          <stop offset="1" stop-color="#3a3a3c"/>
        </linearGradient>
      </defs>
      <rect class="corner-tab" x="1000" y="0" width="50" height="28" fill="url(#cornerTab)"/>
      <path class="grey-swoosh" d="M640 420 Q880 350 1050 298 L1050 318 Q880 365 640 420 Z" fill="url(#greySwoosh)"/>
      <path class="blue-band" d="M0 470 Q620 470 1050 330 L1050 395 Q780 470 520 600 L0 600 Z" fill="url(#blueBand)"/>
    </svg>

    <div class="brand">
      <span class="brand-dot"></span>
      <span class="brand-name">
        <span class="line-main">FLOWMARK</span>
        <span class="line-sub">ENGINEERING</span>
      </span>
    </div>

    <div class="holder">
      <p class="holder-name">DANIEL MORROW</p>
      <p class="holder-role">Managing Director</p>
    </div>

    <ul class="contact-list">
      <li class="contact-item">012 555 0148
        <svg viewBox="0 0 24 24"><path fill="var(--brand-cyan)" d="M6.6 10.8a15 15 0 0 0 6.6 6.6l2.2-2.2c.3-.3.7-.4 1-.2 1.1.4 2.3.6 3.6.6.6 0 1 .4 1 1V20c0 .6-.4 1-1 1A17 17 0 0 1 3 4c0-.6.4-1 1-1h3.5c.6 0 1 .4 1 1 0 1.3.2 2.5.6 3.6.1.3 0 .7-.2 1z"/></svg>
      </li>
      <li class="contact-item">012 555 0172
        <svg viewBox="0 0 24 24"><rect x="6" y="2" width="12" height="20" rx="2" fill="none" stroke="var(--brand-cyan)" stroke-width="2"/><circle cx="12" cy="18" r="1.2" fill="var(--brand-cyan)"/></svg>
      </li>
      <li class="contact-item">012 555 0193
        <svg viewBox="0 0 24 24"><rect x="3" y="9" width="18" height="12" rx="2" fill="var(--brand-cyan)"/><rect x="7" y="3" width="10" height="7" fill="none" stroke="var(--brand-cyan)" stroke-width="2"/></svg>
      </li>
      <li class="contact-item">info@flowmarkeng.com
        <svg viewBox="0 0 24 24"><rect x="2" y="5" width="20" height="14" rx="2" fill="var(--brand-cyan)"/><path d="M3 6l9 7 9-7" fill="none" stroke="#fff" stroke-width="1.8"/></svg>
      </li>
      <li class="contact-item">www.flowmarkeng.com
        <svg viewBox="0 0 24 24"><circle cx="12" cy="12" r="10" fill="var(--brand-cyan)"/><path d="M2 12h20M12 2c3 3 3 17 0 20M12 2c-3 3-3 17 0 20" fill="none" stroke="#fff" stroke-width="1.4"/></svg>
      </li>
    </ul>

    <p class="address">041, 12th floor, Harbour<br>Road NKT</p>
  </article>
</body>
</html>
```